HVAC Company Business Card design with attached logo

Looking for an easily readable and attractive business card design that includes my attached company logo. I selected one sided card because it's more traditional, but I'm open to a 2-sided design. All of the details should be included in the design. Looking to create a professional, upscale image.

Target Market(s)

Commercial and residential consumers

Industry/Entity Type

Hvac

Contact Information for Business Card

Company phone number is 631.487.2953
Company email marcus@tidewellhvac.example
Company name is Bright Harbor Air Conditioning, Refrigeration, and Heating
Marcus Delgado
Owner Operator
Company Address is
PO Box 872,
712 Fenwyck Ln,
Bethpage, NY 11752
Business License K8195240000
Insured

Font styles to use
Serif
Sans Serif

Colors

Designer to choose colors to be used in the design.

Requirements
Must have
• Must include the logo.
Nice to have
• It seems like it should be a one sided card, but I'm open to a 2 sided one.

```html
<!DOCTYPE html>
<html lang="en">
<head>
<meta charset="utf-8">
<title>Bright Harbor Business Card</title>
<link href="https://fonts.googleapis.com/css2?family=Roboto:wght@300;400;700&display=swap" rel="stylesheet">
<style>
  :root {
    --backdrop: #1b1b1c;
    --card: #2a2a2b;
    --card-edge: #333335;
    --white: #f2f2f2;
    --muted: #9a9a9c;
    --blue: #3557c0;
    --orange: #f26a21;
  }
  * { margin: 0; padding: 0; box-sizing: border-box; }
  html, body {
    width: 1200px; height: 1000px; overflow: hidden;
    background: var(--backdrop);
    font-family: "Roboto", Arial, sans-serif;
    color: var(--white);
  }
  .card {
    position: absolute;
    left: 220px;
    width: 760px; height: 434px;
    background: var(--card);
    border: 1px solid var(--card-edge);
    border-radius: 4px;
    box-shadow: 0 18px 40px rgba(0,0,0,.55);
  }
  .card--front { top: 40px; display: flex; align-items: center; justify-content: center; }
  .card--back { top: 520px; }

  .brand { display: flex; align-items: center; gap: 16px; }
  .brand__dot { width: 34px; height: 34px; border-radius: 50%; }
  .brand__name { font-weight: 700; font-size: 54px; letter-spacing: .5px; line-height: 1; }
  .card--front .brand__dot { background: #4a4a4c; }
  .card--front .brand__name { color: #8e8e90; }
  .card--back .brand { position: absolute; left: 46px; top: 180px; gap: 12px; }
  .card--back .brand__dot { width: 26px; height: 26px; background: var(--orange); }
  .card--back .brand__name { font-size: 38px; color: var(--blue); }

  .divider {
    position: absolute; left: 420px; top: 110px;
    width: 2px; height: 210px; background: var(--white);
  }
  .details { position: absolute; left: 458px; top: 106px; }
  .person__name { color: var(--blue); font-weight: 700; font-size: 27px; letter-spacing: .5px; }
  .person__role { color: var(--orange); font-weight: 700; font-size: 16px; margin-top: 4px; letter-spacing: .5px; }
  .address { font-weight: 300; font-size: 16px; line-height: 1.3; margin-top: 20px; }
  .contacts { list-style: none; margin-top: 14px; }
  .contacts li { display: flex; align-items: center; gap: 14px; font-size: 16px; font-weight: 300; margin-bottom: 6px; }
  .contacts svg { width: 16px; height: 16px; flex: none; }
  .accent { color: var(--orange); }
  .license {
    position: absolute; right: 40px; bottom: 34px;
    font-size: 17px; letter-spacing: 1.5px;
  }
</style>
</head>
<body>
  <section class="card card--front">
    <div class="brand">
      <span class="brand__dot"></span>
      <span class="brand__name">Bright Harbor</span>
    </div>
  </section>

  <section class="card card--back">
    <div class="brand">
      <span class="brand__dot"></span>
      <span class="brand__name">Bright Harbor</span>
    </div>
    <div class="divider"></div>
    <div class="details">
      <p class="person__name">Marcus Delgado</p>
      <p class="person__role">Owner Operator</p>
      <p class="address">PO Box 872, 712 Fenwyck Ln,<br>Bethpage, NY 11752</p>
      <ul class="contacts">
        <li>
          <svg viewBox="0 0 16 16" aria-hidden="true"><path d="M4 1l3 3-2 2c1 2 3 4 5 5l2-2 3 3-2 2C7 14 2 9 2 3z" fill="none" stroke="var(--orange)" stroke-width="1.6"/></svg>
          631.487.2953
        </li>
        <li>
          <svg viewBox="0 0 16 16" aria-hidden="true"><rect x="1" y="3" width="14" height="10" fill="var(--orange)"/><path d="M1 3l7 6 7-6" fill="none" stroke="var(--card)" stroke-width="1.3"/></svg>
          marcus@tidewellhvac.example
        </li>
        <li>
          <svg viewBox="0 0 16 16" aria-hidden="true"><g fill="none" stroke="var(--orange)" stroke-width="1.3"><circle cx="8" cy="8" r="6.5"/><ellipse cx="8" cy="8" rx="3" ry="6.5"/><path d="M1.5 8h13"/></g></svg>
          <span>www.<span class="accent">tidewellhvac</span>.example</span>
        </li>
      </ul>
    </div>
    <p class="license">License K8195240000</p>
  </section>
</body>
</html>
```